BrivoTerna. Lantern of the Steady Harvest. Business card

Professional business card for BrivoTerna (Lantern of the Steady Harvest)
My rationale: Strategy-> Execution-> Results-> Value that lead to the BrivoTerna name: We put the Lantern of the Steady Harvest.
We deliver value to our customers helping them at defining a good strategy (cyan arrow). 90% of well formulated strategies fail due to poor execution so we also consider strategical execution very important (green arrow). Due to the execution we obtain the results (blue arrow). Finally, the results provide feedback to redefine strategy, and the new strategy has to be executed and new results obtained providing new feedback and on and on. It's like a wheel that finally, must create corporate value: value for shareholders, staholders, employees, providers...-

Target Market(s)

CEOs and steering comitees , invewrnent funds

Industry/Entity Type

Business Consultant

Contact Information for Business Card

Teodoro Vinsquel
CEO & Founder
teodoro.vinsquel@brivoterna-example.com
Mobile: +34 655.803.912
www.brivoterna-example.com

Colors

Designer to choose colors to be used in the design.

Requirements
Nice to have
• Nice to hace the words: Strategy, execution, results
• Nice to vave the claim: Lantern of the Steady Harvest
• The three colors should be shown:
• cyan for STRATEGY
• green for EXECUTION
• blue for RESULTS
Should not have
• Complete black background

```html
<!DOCTYPE html>
<html lang="en">
<head>
<meta charset="utf-8">
<title>BrivoTerna – Business Card</title>
<link href="https://fonts.googleapis.com/css2?family=Montserrat:wght@400;500;700;800&display=swap" rel="stylesheet">
<style>
  :root {
    --backdrop: #2a2c31;
    --royal: #0a2fa6;
    --royal-deep: #06248a;
    --navy: #123a94;
    --cyan: #1d9fe3;
    --green: #8dc04a;
    --ink: #2b2b2b;
    --grey: #5b5f66;
    --paper: #ffffff;
  }
  * { margin: 0; padding: 0; box-sizing: border-box; }
  html, body { width: 1200px; height: 852px; overflow: hidden; }
  body {
    background: var(--backdrop);
    font-family: "Montserrat", sans-serif;
    position: relative;
  }
  .card {
    position: absolute;
    width: 540px;
    height: 309px;
    border-radius: 18px;
    overflow: hidden;
    box-shadow: 0 14px 34px rgba(0,0,0,.45);
  }
  .card--front {
    left: 50px;
    top: 110px;
    background: linear-gradient(135deg, var(--royal) 0%, var(--royal-deep) 100%);
  }
  .card--back {
    left: 610px;
    top: 433px;
    background: var(--paper);
  }
  .wordmark {
    position: absolute;
    display: flex;
    align-items: center;
    gap: 10px;
    font-weight: 800;
    letter-spacing: -0.5px;
  }
  .wordmark__dot {
    width: 16px; height: 16px; border-radius: 50%;
    background: var(--green);
  }
  .card--front .wordmark {
    left: 52px; top: 168px;
    font-size: 40px;
    color: var(--paper);
  }
  .card--back .wordmark {
    left: 40px; top: 48px;
    font-size: 38px;
    color: var(--navy);
  }
  .person {
    position: absolute;
    left: 40px; top: 128px;
  }
  .person__name {
    font-size: 23px;
    font-weight: 700;
    color: var(--cyan);
  }
  .person__role {
    font-size: 14px;
    font-weight: 500;
    color: var(--grey);
    margin-top: 2px;
  }
  .contacts {
    position: absolute;
    left: 40px; top: 198px;
    list-style: none;
  }
  .contacts li {
    display: flex;
    align-items: center;
    gap: 9px;
    font-size: 14px;
    color: var(--ink);
    line-height: 24px;
  }
  .contacts svg { width: 12px; height: 12px; flex: none; }
  .accent-bar {
    position: absolute;
    left: 0; top: 196px;
    width: 8px; height: 50px;
    background: var(--green);
  }
</style>
</head>
<body>
  <section class="card card--front" aria-label="Business card front">
    <div class="wordmark"><span class="wordmark__dot"></span>BrivoTerna</div>
  </section>

  <section class="card card--back" aria-label="Business card back">
    <div class="wordmark"><span class="wordmark__dot"></span>BrivoTerna</div>
    <div class="person">
      <p class="person__name">Teodoro Vinsquel</p>
      <p class="person__role">CEO &amp; Founder</p>
    </div>
    <span class="accent-bar"></span>
    <ul class="contacts">
      <li>
        <svg viewBox="0 0 12 12" aria-hidden="true"><path d="M2.5 1 L4.5 1 L5.3 3.5 L4 4.4 C4.6 5.8 6.2 7.4 7.6 8 L8.5 6.7 L11 7.5 L11 9.5 C11 10.3 10.3 11 9.5 11 C5 11 1 7 1 2.5 C1 1.7 1.7 1 2.5 1 Z" fill="var(--cyan)"/></svg>
        +34 655.803.912
      </li>
      <li>
        <svg viewBox="0 0 12 12" aria-hidden="true"><rect x="1" y="2.5" width="10" height="7" rx="1" fill="none" stroke="var(--cyan)" stroke-width="1.3"/><path d="M1.5 3 L6 6.5 L10.5 3" fill="none" stroke="var(--cyan)" stroke-width="1.3"/></svg>
        teodoro.vinsquel@brivoterna-example.com
      </li>
      <li>
        <svg viewBox="0 0 12 12" aria-hidden="true"><circle cx="6" cy="6" r="5" fill="none" stroke="var(--cyan)" stroke-width="1.2"/><ellipse cx="6" cy="6" rx="2.2" ry="5" fill="none" stroke="var(--cyan)" stroke-width="1"/><path d="M1 6 H11" stroke="var(--cyan)" stroke-width="1"/></svg>
        www.brivoterna-example.com
      </li>
    </ul>
  </section>
</body>
</html>
```